We need a new business card that reflects who we are. Professional, classy, modern, and service ori

We need a business card design for a window coverings design company in Kansas City called Bright Lane Interiors. We offer professional, modern, and high quality window covering products. We are looking to portray an image of a big, national franchise. We are a 5 location (with showrooms) business with 10 professional designers and 4 professional installers. These cards will be used with Thank you cards, given to realtors, and asked for referrals with.

Target Market(s)

Kansas City

Industry/Entity Type

Business

Contact Information for Business Card

We would like our card to look clean and simple on the front, featuring our logo and Marlow Fenwick's. Our designers' phone numbers and emails should be displayed as well as their title.

Font styles to use
Sans Serif

Colors

Designer to choose colors to be used in the design.

Requirements
Must have
• Front - Logos, name, phone number, email address
• Back - Showroom locations, social media? Appt date/time?
Nice to have
• I would like a clean and modern look (not contemporary. I like a white background, but I am open to ideas. Looking for a "National chain" look for a small business.
Should not have
• Too much busyness.

```html
<!DOCTYPE html>
<html lang="en">
<head>
<meta charset="utf-8">
<title>Bright Lane Interiors – Business Card</title>
<link href="https://fonts.googleapis.com/css2?family=Roboto:wght@400;500&family=Roboto+Condensed:wght@400;500&display=swap" rel="stylesheet">
<style>
  :root {
    --backdrop: #2b2b2b;
    --card: #f3f3f3;
    --brand-red: #c8373d;
    --ink: #1c1c1c;
    --text-grey: #4a4a4a;
    --partner-grey: #6b7079;
    --accent-orange: #ee7d1a;
    --rule: #777777;
  }
  * { margin: 0; padding: 0; box-sizing: border-box; }
  html, body { width: 1200px; height: 960px; overflow: hidden; }
  body {
    background: var(--backdrop);
    position: relative;
    font-family: "Roboto", sans-serif;
  }
  .card {
    position: absolute;
    width: 600px;
    height: 342px;
    background: var(--card);
    box-shadow: 0 3px 8px rgba(0,0,0,.45);
  }
  .card-front { left: 322px; top: 108px; }
  .card-back { left: 320px; top: 493px; }

  /* Front */
  .brand {
    position: absolute;
    top: 62px; left: 0; right: 0;
    text-align: center;
  }
  .brand-name {
    display: inline-flex;
    align-items: center;
    gap: 12px;
    font-weight: 500;
    font-size: 34px;
    color: var(--ink);
    letter-spacing: .5px;
  }
  .brand-mark {
    width: 26px; height: 26px;
    background: var(--brand-red);
  }
  .brand-tagline {
    margin-top: 12px;
    font-size: 13px;
    color: var(--ink);
  }
  .designer {
    position: absolute;
    top: 256px; left: 0; right: 0;
    text-align: center;
    font-family: "Roboto Condensed", sans-serif;
  }
  .designer-name {
    font-size: 25px;
    font-weight: 500;
    color: var(--brand-red);
  }
  .designer-title {
    font-family: "Roboto", sans-serif;
    font-size: 16px;
    font-weight: 500;
    color: var(--ink);
  }
  .contact {
    position: absolute;
    top: 287px; left: 0; right: 0;
    text-align: center;
    font-size: 15px;
    color: var(--text-grey);
  }

  /* Back */
  .partner {
    position: absolute;
    top: 40px; left: 0; right: 0;
    display: flex; justify-content: center; align-items: center; gap: 5px;
    font-size: 14px;
    font-weight: 500;
    color: var(--partner-grey);
  }
  .partner-dot {
    width: 20px; height: 20px; border-radius: 50%;
    background: var(--accent-orange);
  }
  .appointments {
    position: absolute;
    top: 82px; left: 82px;
    width: 424px;
  }
  .appt-row {
    display: flex;
    align-items: baseline;
    height: 45.5px;
    color: var(--brand-red);
  }
  .appt-label { font-size: 16px; white-space: nowrap; }
  .appt-fill {
    border-bottom: 1px dotted var(--rule);
    margin: 0 2px 0 5px;
    transform: translateY(-4px);
  }
  .appt-fill.date { width: 168px; }
  .appt-fill.time { width: 104px; }
  .appt-unit { font-size: 13px; margin-left: 4px; white-space: nowrap; }
  .showrooms {
    position: absolute;
    top: 259px; left: 0; right: 0;
    text-align: center;
    font-family: "Roboto Condensed", sans-serif;
  }
  .showrooms-title {
    font-size: 16px; font-weight: 500; color: var(--brand-red);
  }
  .showrooms-list {
    margin-top: 3px;
    font-size: 14px; color: var(--text-grey);
  }
  .social {
    position: absolute;
    top: 302px; left: 0; right: 0;
    display: flex; justify-content: center; gap: 3px;
  }
  .social-dot {
    width: 20px; height: 20px; border-radius: 50%;
    background: var(--brand-red);
  }
</style>
</head>
<body>
  <section class="card card-front">
    <div class="brand">
      <div class="brand-name"><span class="brand-mark"></span>Bright Lane Interiors</div>
      <p class="brand-tagline">Blinds, Shades, Shutters, Draperies &amp; Decor</p>
    </div>
    <div class="designer">
      <span class="designer-name">JORDAN ELLIS -</span>
      <span class="designer-title">DESIGNER</span>
    </div>
    <p class="contact">913.555.0148 | info@brightlaneinteriors.com | brightlaneinteriors.com</p>
  </section>

  <section class="card card-back">
    <div class="partner"><span>Marlow Fenwick Gallery</span><span class="partner-dot"></span></div>
    <div class="appointments">
      <div class="appt-row"><span class="appt-label">Date :</span><span class="appt-fill date"></span><span class="appt-label">Time :</span><span class="appt-fill time"></span><span class="appt-unit">AM/PM</span></div>
      <div class="appt-row"><span class="appt-label">Date :</span><span class="appt-fill date"></span><span class="appt-label">Time :</span><span class="appt-fill time"></span><span class="appt-unit">AM/PM</span></div>
      <div class="appt-row"><span class="appt-label">Date :</span><span class="appt-fill date"></span><span class="appt-label">Time :</span><span class="appt-fill time"></span><span class="appt-unit">AM/PM</span></div>
      <div class="appt-row"><span class="appt-label">Date :</span><span class="appt-fill date"></span><span class="appt-label">Time :</span><span class="appt-fill time"></span><span class="appt-unit">AM/PM</span></div>
    </div>
    <div class="showrooms">
      <p class="showrooms-title">SHOWROOM LOCATIONS</p>
      <p class="showrooms-list">ASHFORD | MAPLE RIDGE | CEDAR HOLLOW | NORTHGATE | ST ALBION</p>
    </div>
    <div class="social" aria-label="Social media">
      <span class="social-dot"></span><span class="social-dot"></span><span class="social-dot"></span><span class="social-dot"></span>
    </div>
  </section>
</body>
</html>
```